Oven Cleaning flyer design

Hi there,
I need help designing a letterbox flyer. It needs to be DL size.
I have attached a rough design made with Chat GPT.
Would like back and front, have my business colors.
Please find attached mock up of what I would roughly like.
Also find attached logo.
Thank you

Target Market(s)

Home owners over 40

Industry/Entity Type

Cleaning

Requirements
Must have
• Logo, before after of oven, brand colors

```html
<!DOCTYPE html>
<html lang="en">
<head>
<meta charset="utf-8">
<title>Gleam Oven Care – DL Flyer</title>
<link rel="stylesheet" href="https://fonts.googleapis.com/css2?family=Poppins:wght@400;500;600;700;800&display=swap">
<style>
  :root{
    --navy:#161b4d;
    --teal:#4aa5a8;
    --teal-dark:#2e7479;
    --teal-deep:#24555a;
    --aqua:#4cc4cf;
    --aqua-light:#7fd8de;
    --red:#cf151b;
    --white:#ffffff;
    --black:#0b0b0d;
    --stage:#a6a6a6;
    --font:'Poppins', sans-serif;
  }
  *{box-sizing:border-box;margin:0;padding:0}
  html,body{width:1032px;height:1200px;overflow:hidden}
  body{background:var(--stage);font-family:var(--font);position:relative}

  .flyer{position:absolute;top:262px;width:334px;height:706px;background:var(--white);overflow:hidden}
  .flyer--front{left:136px}
  .flyer--back{left:573px}

  .abs{position:absolute}
  .brand{display:flex;align-items:center;gap:8px;color:var(--teal);font-weight:700;font-size:19px;letter-spacing:.5px;white-space:nowrap}
  .brand__dot{width:14px;height:14px;border-radius:50%;background:var(--navy)}

  .wave{position:absolute;left:0;width:334px}

  /* front */
  .front__kicker{top:104px;left:0;width:334px;text-align:center;color:var(--navy);font-weight:700;font-size:24px}
  .front__title{top:118px;left:0;width:334px;text-align:center;color:var(--navy);font-weight:800;font-size:74px;line-height:1.1;letter-spacing:-1px}
  .front__sub{top:200px;left:0;width:334px;text-align:center;color:var(--navy);font-weight:700;font-size:29px}
  .front__copy{top:246px;left:36px;width:262px;text-align:center;color:var(--navy);font-size:11.6px;line-height:1.08}

  .snap{position:absolute;background:var(--white);padding:6px 6px 0;box-shadow:0 3px 8px rgba(0,0,0,.25)}
  .snap__photo{width:100%;height:140px}
  .snap__label{height:30px;display:flex;align-items:center;justify-content:center;color:var(--navy);font-weight:700;font-size:16px}
  .snap--before{left:17px;top:326px;width:146px;transform:rotate(-3deg)}
  .snap--after{left:156px;top:323px;width:146px;transform:rotate(3deg)}
  .photo--grill-dirty{background:linear-gradient(160deg,#8a8f90,#3b3a36 55%,#5b4a3c)}
  .photo--grill-clean{background:linear-gradient(160deg,#9ea3a3,#3c3e40 55%,#55585b)}

  .front__call{top:520px;left:0;width:334px;text-align:center;color:var(--white);font-size:30px;font-weight:400}
  .pill{position:absolute;background:var(--navy);color:var(--white);border-radius:7px;display:flex;align-items:center;justify-content:center;font-size:18px}
  .front__pill{top:567px;left:29px;width:275px;height:33px}

  .phonebar{position:absolute;top:611px;left:0;width:334px;height:45px;background:var(--black);display:flex;align-items:center;justify-content:center;gap:10px;color:var(--white);font-weight:700;font-size:31px}
  .web{position:absolute;top:662px;left:0;width:334px;display:flex;align-items:center;justify-content:center;gap:6px;color:var(--white);font-size:14px}

  /* back */
  .back__title{top:90px;left:28px;width:160px;color:var(--navy);font-weight:700;font-size:16.5px;line-height:1.1}
  .back__copy{top:133px;left:30px;width:150px;color:var(--navy);font-size:11.6px;line-height:1.08}
  .back__person{top:58px;left:140px;width:194px;height:200px;background:linear-gradient(180deg,#e9ecef,#c7ced6 50%,#1d2a4a);}

  .features{top:252px;left:28px;width:136px;list-style:none}
  .feature{display:flex;align-items:center;gap:10px;height:42px;border-bottom:1px solid rgba(255,255,255,.35);color:var(--white);font-size:12px;line-height:1.15}
  .feature:last-child{border-bottom:none}
  .feature__icon{flex:none;width:30px;height:30px;border-radius:50%;background:var(--navy);display:flex;align-items:center;justify-content:center}

  .offer{top:245px;left:181px;width:120px;height:120px;border-radius:50%;background:var(--red);border:3px solid rgba(255,255,255,.85);color:var(--white);text-align:center;padding-top:17px}
  .offer__lead{font-size:11px;line-height:1.1}
  .offer__amount{font-weight:700;font-size:32px;line-height:1.05}
  .offer__amount small{font-size:14px}
  .offer__amount sup{font-size:16px}
  .offer__tail{font-weight:600;font-size:9px;line-height:1.1}

  .compare{top:384px;left:28px;width:276px;height:126px;border-radius:6px;background:var(--white);padding:4px;display:flex;gap:4px}
  .compare__photo{flex:1;border-radius:3px}
  .photo--oven-dirty{background:linear-gradient(180deg,#f3f1ee 0 14%,#1b1b1b 14% 30%,#5a5650 60%,#2a2724)}
  .photo--oven-clean{background:linear-gradient(180deg,#f3f1ee 0 14%,#1b1b1b 14% 30%,#3f4346 60%,#1e2022)}
  .tag{position:absolute;height:21px;border-radius:3px;background:var(--aqua);color:var(--navy);font-weight:600;font-size:13px;display:flex;align-items:center;justify-content:center}
  .tag--before{top:502px;left:60px;width:68px}
  .tag--after{top:502px;left:197px;width:68px}

  .also{top:546px;left:111px;width:111px;height:22px;border-radius:3px 3px 0 0;background:var(--aqua);color:var(--navy);font-weight:600;font-size:11.5px;display:flex;align-items:center;justify-content:center}
  .also-list{top:568px;left:29px;width:275px;height:37px;border-radius:4px;background:var(--navy);display:flex;list-style:none}
  .also-list li{flex:1;display:flex;flex-direction:column;align-items:center;justify-content:center;color:var(--white);font-size:11.5px;border-right:1px solid rgba(255,255,255,.3)}
  .also-list li:last-child{border-right:none}
</style>
</head>
<body>

<!-- FRONT -->
<section class="flyer flyer--front">
  <svg class="wave" style="top:380px;height:326px" viewBox="0 0 334 326" preserveAspectRatio="none">
    <defs>
      <linearGradient id="tealFront" x1="0" y1="0" x2="0" y2="1">
        <stop offset="0" stop-color="#4fadb0"/><stop offset="1" stop-color="#2f7479"/>
      </linearGradient>
    </defs>
    <path d="M0 18 C80 34 200 -6 334 22 L334 326 L0 326Z" fill="var(--navy)"/>
    <path d="M0 30 C90 46 200 10 334 36 L334 326 L0 326Z" fill="url(#tealFront)"/>
  </svg>

  <div class="abs brand" style="top:42px;left:84px"><span class="brand__dot"></span>Gleam Oven Care</div>
  <p class="abs front__kicker">Bring Your</p>
  <h1 class="abs front__title">Oven</h1>
  <p class="abs front__sub">Back to Life</p>
  <p class="abs front__copy">Professional, non-caustic oven cleaning that removes built-up grease, smoke, and burnt grime - leaving your oven looking fresh again.</p>

  <figure class="snap snap--before">
    <div class="snap__photo photo--grill-dirty" role="img" aria-label="Grill plate covered in grease before cleaning"></div>
    <figcaption class="snap__label">BEFORE</figcaption>
  </figure>
  <figure class="snap snap--after">
    <div class="snap__photo photo--grill-clean" role="img" aria-label="Same grill plate clean after service"></div>
    <figcaption class="snap__label">AFTER</figcaption>
  </figure>

  <p class="abs front__call">Call Now for</p>
  <div class="pill front__pill">Fast, Professional Service</div>

  <div class="phonebar">
    <svg width="26" height="26" viewBox="0 0 24 24"><path d="M6.6 10.8a15 15 0 0 0 6.6 6.6l2.2-2.2a1 1 0 0 1 1-.25 11.4 11.4 0 0 0 3.6.6 1 1 0 0 1 1 1V20a1 1 0 0 1-1 1A17 17 0 0 1 3 4a1 1 0 0 1 1-1h3.5a1 1 0 0 1 1 1c0 1.25.2 2.45.6 3.6a1 1 0 0 1-.25 1z" fill="var(--aqua)"/></svg>
    0400 123 456
  </div>
  <div class="web">
    <svg width="14" height="14" viewBox="0 0 24 24"><circle cx="12" cy="12" r="10" fill="none" stroke="#fff" stroke-width="2"/><path d="M2 12h20M12 2c3 3 3 17 0 20M12 2c-3 3-3 17 0 20" fill="none" stroke="#fff" stroke-width="1.6"/></svg>
    www.gleamovencare.com.au
  </div>
</section>

<!-- BACK -->
<section class="flyer flyer--back">
  <div class="abs back__person" role="img" aria-label="Technician in navy uniform giving a thumbs up"></div>

  <svg class="wave" style="top:222px;height:484px" viewBox="0 0 334 484" preserveAspectRatio="none">
    <defs>
      <linearGradient id="tealBack" x1="0" y1="0" x2="0" y2="1">
        <stop offset="0" stop-color="#4fadb0"/><stop offset=".7" stop-color="#2f7479"/><stop offset="1" stop-color="#24474b"/>
      </linearGradient>
    </defs>
    <path d="M0 12 C70 -4 120 0 170 14 C230 30 290 26 334 10 L334 484 L0 484Z" fill="var(--navy)"/>
    <path d="M0 24 C70 8 120 12 170 26 C230 42 290 38 334 22 L334 484 L0 484Z" fill="url(#tealBack)"/>
  </svg>

  <div class="abs brand" style="top:42px;left:36px"><span class="brand__dot"></span>Gleam Oven Care</div>
  <h2 class="abs back__title">Why Choose Gleam Oven Care?</h2>
  <p class="abs back__copy">Professional, non-caustic oven cleaning that lifts grease, smoke, and burnt grime - leaving your oven looking fresh again.</p>

  <ul class="abs features">
    <li class="feature">
      <span class="feature__icon"><svg width="16" height="16" viewBox="0 0 24 24"><path d="M12 2l8 3v6c0 5-3.5 9-8 11-4.5-2-8-6-8-11V5z" fill="#fff"/><path d="M8 12l3 3 5-6" fill="none" stroke="var(--navy)" stroke-width="2"/></svg></span>
      Reliable Service
    </li>
    <li class="feature">
      <span class="feature__icon"><svg width="16" height="16" viewBox="0 0 24 24"><circle cx="9" cy="14" r="6" fill="#fff"/><circle cx="17" cy="7" r="4" fill="#fff"/></svg></span>
      Non-Caustic<br>Cleaning
    </li>
    <li class="feature">
      <span class="feature__icon"><svg width="16" height="16" viewBox="0 0 24 24"><path d="M12 3l2.6 5.6 6 .7-4.5 4.1 1.2 6L12 16.4 6.7 19.4l1.2-6L3.4 9.3l6-.7z" fill="#fff"/></svg></span>
      Satisfaction<br>Guaranteed
    </li>
  </ul>

  <div class="abs offer">
    <p class="offer__lead">Mention this<br>flyer for</p>
    <p class="offer__amount"><sup>$</sup>10<small>OFF</small></p>
    <p class="offer__tail">YOUR FIRST<br>CLEAN</p>
  </div>

  <div class="abs compare">
    <div class="compare__photo photo--oven-dirty" role="img" aria-label="Open oven with heavy burnt grime before cleaning"></div>
    <div class="compare__photo photo--oven-clean" role="img" aria-label="Same oven interior clean after service"></div>
  </div>
  <div class="tag tag--before">BEFORE</div>
  <div class="tag tag--after">AFTER</div>

  <div class="abs also">We also clean</div>
  <ul class="abs also-list">
    <li><svg width="9" height="9" viewBox="0 0 24 24"><circle cx="12" cy="12" r="12" fill="var(--aqua)"/><path d="M6 12l4 4 8-8" fill="none" stroke="#fff" stroke-width="3"/></svg>Cooktops</li>
    <li><svg width="9" height="9" viewBox="0 0 24 24"><circle cx="12" cy="12" r="12" fill="var(--aqua)"/><path d="M6 12l4 4 8-8" fill="none" stroke="#fff" stroke-width="3"/></svg>Rangehoods</li>
    <li><svg width="9" height="9" viewBox="0 0 24 24"><circle cx="12" cy="12" r="12" fill="var(--aqua)"/><path d="M6 12l4 4 8-8" fill="none" stroke="#fff" stroke-width="3"/></svg>BBQs</li>
  </ul>

  <div class="phonebar">
    <svg width="26" height="26" viewBox="0 0 24 24"><path d="M6.6 10.8a15 15 0 0 0 6.6 6.6l2.2-2.2a1 1 0 0 1 1-.25 11.4 11.4 0 0 0 3.6.6 1 1 0 0 1 1 1V20a1 1 0 0 1-1 1A17 17 0 0 1 3 4a1 1 0 0 1 1-1h3.5a1 1 0 0 1 1 1c0 1.25.2 2.45.6 3.6a1 1 0 0 1-.25 1z" fill="var(--aqua)"/></svg>
    0400 123 456
  </div>
  <div class="web">
    <svg width="14" height="14" viewBox="0 0 24 24"><circle cx="12" cy="12" r="10" fill="none" stroke="#fff" stroke-width="2"/><path d="M2 12h20M12 2c3 3 3 17 0 20M12 2c-3 3-3 17 0 20" fill="none" stroke="#fff" stroke-width="1.6"/></svg>
    www.gleamovencare.com.au
  </div>
</section>

</body>
</html>
```